Business Cards for new orthopaedic surgery practice

My husband and I are starting our own orthopaedic surgery practice. We are looking for a business card that is uniform, but one will have my name/title and the other will have his. You can just create one design with my name on it for now. But when I choose your design as the winning design I will ask that you add another copy with his name/title.

We are looking for classy, simple, elite all in one. We like dark blues/a little gold/yellow. Something that goes with our logo. We want our logo incorporated. Here is all the info you need:
Business name: RV Bone & Vitality Center
Location: 38517 North Willowmere Ave
Palm Hollow, FL 33990
Phone: 954-218-4063
Fax: 954-582-7341
Email: info@myrvbonecare.example

Names: Lydia Vance, M.D.
Board Certified Hand and Upper Extremity Surgeon

Ebo Dansu, M.D.
Board Certified Hip & Knee Replacement/General Orthopaedic Surgeon

Can decide what you want to put on the back. Maybe a slogan:
Grounded in Skill. Centered on You

I am just going to upload our logo. The only thing is if we select you as the winning design, the location, and phone numbers may change. We will need your help to update that once fully solidified.

Industry/Entity Type

Medical

Contact Information for Business Card

Colors
0054AA
0677BA
7BADD7
CADEEF
E8F1F8
0094D4
00A9DD
6FCCEA
C7EBF8
E9F6FB

Requirements
Must have
• class, appeal,
Should not have
• We want to air on the side of masculine if we are looking at masculine vs. feminine feel. But we still want it classy, sophisticated, and something we will love

```html
<!DOCTYPE html>
<html lang="en">
<head>
<meta charset="utf-8">
<title>RV Bone &amp; Vitality Center – Business Cards</title>
<link rel="stylesheet" href="https://fonts.googleapis.com/css2?family=Montserrat:wght@400;500;700&display=swap">
<style>
  :root {
    --backdrop: #2b2b2d;
    --navy: #1c2a52;
    --gold: #c9a25a;
    --white: #ffffff;
    --text-soft: #e8ebf2;
  }
  * { box-sizing: border-box; margin: 0; padding: 0; }
  html, body { width: 1200px; height: 875px; overflow: hidden; }
  body {
    background: var(--backdrop);
    font-family: "Montserrat", Arial, sans-serif;
    color: var(--white);
    display: flex;
    flex-direction: column;
    align-items: center;
    justify-content: center;
    gap: 25px;
  }
  .card {
    position: relative;
    width: 700px;
    height: 400px;
    background: var(--navy);
    border-radius: 24px;
    overflow: hidden;
  }

  /* brand mark: name beside one plain circle */
  .brand {
    display: flex;
    align-items: center;
    gap: 14px;
    font-weight: 500;
    color: var(--white);
    letter-spacing: 0.04em;
    text-transform: uppercase;
  }
  .brand__dot {
    flex: none;
    border: 2px solid var(--gold);
    border-radius: 50%;
  }

  /* front side */
  .card--front .brand {
    position: absolute;
    left: 0; right: 0; top: 130px;
    justify-content: center;
    font-size: 22px;
  }
  .card--front .brand__dot { width: 40px; height: 40px; }
  .slogan {
    position: absolute;
    left: 0; right: 0; top: 270px;
    text-align: center;
    font-size: 19px;
    font-weight: 400;
    letter-spacing: 0.02em;
  }

  /* details side */
  .card--details .brand {
    position: absolute;
    left: 40px; top: 160px;
    width: 250px;
    font-size: 17px;
    line-height: 1.35;
  }
  .card--details .brand__dot { width: 34px; height: 34px; }
  .divider {
    position: absolute;
    left: 318px; top: 80px;
    width: 1px; height: 220px;
    background: var(--gold);
  }
  .details {
    position: absolute;
    left: 348px; top: 78px;
    font-size: 15px;
    line-height: 1.3;
    color: var(--text-soft);
  }
  .details__name {
    font-size: 22px;
    font-weight: 700;
    color: var(--gold);
    margin-bottom: 2px;
  }
  .details__title { margin-bottom: 18px; }
  .details__address { margin-bottom: 18px; }
  .contact { list-style: none; }
  .contact li { display: flex; align-items: center; gap: 10px; }
  .contact svg { width: 13px; height: 13px; fill: var(--gold); flex: none; }
  .gold-band {
    position: absolute;
    left: 0; right: 0; bottom: 0;
    height: 12px;
    background: var(--gold);
  }
</style>
</head>
<body>

  <section class="card card--front">
    <div class="brand"><span class="brand__dot"></span>RV Bone &amp; Vitality Center</div>
    <p class="slogan">Grounded in Skill. Centered on You</p>
  </section>

  <section class="card card--details">
    <div class="brand"><span class="brand__dot"></span>RV Bone &amp; Vitality Center</div>
    <div class="divider"></div>
    <div class="details">
      <p class="details__name">Lydia Vance, M.D.</p>
      <p class="details__title">Board Certified Hand and<br>Upper Extremity Surgeon</p>
      <p class="details__address">38517 North Willowmere Ave<br>Palm Hollow, FL 33990</p>
      <ul class="contact">
        <li><svg viewBox="0 0 24 24"><path d="M6.6 10.8a15.1 15.1 0 0 0 6.6 6.6l2.2-2.2a1 1 0 0 1 1-.25 11.4 11.4 0 0 0 3.6.57 1 1 0 0 1 1 1V20a1 1 0 0 1-1 1A17 17 0 0 1 3 4a1 1 0 0 1 1-1h3.5a1 1 0 0 1 1 1c0 1.25.2 2.45.57 3.57a1 1 0 0 1-.25 1z"/></svg>954-218-4063</li>
        <li><svg viewBox="0 0 24 24"><path d="M6 2h10v5H6zM4 8h16a2 2 0 0 1 2 2v7h-4v5H6v-5H2v-7a2 2 0 0 1 2-2zm4 9v3h8v-3z"/></svg>954-582-7341</li>
        <li><svg viewBox="0 0 24 24"><path d="M2 5h20v14H2zm2 2v.5l8 5 8-5V7l-8 5z"/></svg>info@myrvbonecare.example</li>
      </ul>
    </div>
    <div class="gold-band"></div>
  </section>

</body>
</html>
```